CD Cover für junge Pop-Rock Band
Sehr kreative vorschläge. mehrere designs, die alle unter den top-favoriten für uns waren. änderungen und anpassungen stets schnell umgesetzt und auch nach gewinner-auswahl noch weiter zusammen gearbeitet bevor das endgültige design übergeben wurde.
Zielgruppe
Wir sind eine junge Band aus München und machen ausschließlich eigene Songs im Bereich Pop-Rock. Durch Einflüsse aus verschiedenen anderen Genres wie Funk, Reggae und Britpop grenzen sich unsere Songs von typischem Mainstream-Pop ab. Unsere Zielgruppe setzt sich aus Personen verschiedener Altersgruppen zusammen, der Fokus liegt jedoch auf Mitte Zwanzig- bis Mitte Dreißig-Jährigen.
Homepage: www.okapimind.com
Sozialnetz: www.sozialnetz.example/okapimindband
Aufgabenstellung
Wir benötigen ein Design für unsere neue EP "Open Gates". Diese wird in Form eines DigiPacks veröffentlicht werden. Daher werden Designs für Vorderseite, Rückseite, zwei Innenseiten sowie die CD selbst benötigt.
Folgendes sollte auf den jeweiligen Seiten enthalten sein:
Vorderseite:
- Bandschriftzug (siehe Anhang)
- Name der EP: Open Gates
Rückseite:
- Trackliste (1.Velvet Spoon, 2.Hold It Near, 3.Harbor Pike, 4.Can We Stay, 5.Brightest Edge)
- Credits (Recording by ..., Mix by ..., Mastering by ..., etc. -> wird noch festgesetzt)
Anmerkung:
Die roten Kratzer aus dem Bandlogo können bei Bedarf frei verwendet werden hinsichtlich Farbe, Muster, Gestaltung, Größe, etc.
Wir möchten keine Bilder von uns (z.B. von unserer Homepage, Sozialnetz, etc) auf der CD.

```html
<!DOCTYPE html>
<html lang="de">
<head>
<meta charset="utf-8">
<title>Okapimind – Open Gates DigiPack</title>
<link rel="stylesheet" href="https://fonts.googleapis.com/css2?family=Oswald:wght@300;400&family=Lexend+Exa:wght@600&display=swap">
<style>
  :root {
    --page: #e6e6e1;
    --ice: #eef2f6;
    --sky: #b9cddd;
    --steel: #4f7ea6;
    --navy: #2c4a6b;
    --slate: #3b4350;
    --taupe: #ad968c;
    --title-blue: #5d8cbf;
    --ink: #1f2630;
    --white: #ffffff;
  }
  * { box-sizing: border-box; margin: 0; padding: 0; }
  html, body { width: 1066px; height: 1200px; overflow: hidden; background: var(--page); }
  .sheet { position: relative; width: 1066px; height: 1200px; }
  .panel {
    position: absolute; width: 320px; height: 285px; overflow: hidden;
    box-shadow: 0 2px 5px rgba(0,0,0,.25);
  }
  .art { position: absolute; inset: 0; }
  .art--front {
    background:
      radial-gradient(ellipse 60% 45% at 25% 20%, var(--ice), transparent 70%),
      radial-gradient(ellipse 40% 40% at 85% 25%, var(--slate), transparent 75%),
      radial-gradient(ellipse 45% 45% at 85% 75%, var(--taupe), transparent 75%),
      linear-gradient(180deg, var(--sky) 0%, var(--ice) 30%, var(--steel) 62%, var(--navy) 85%, var(--sky) 100%);
  }
  .art--back {
    background:
      radial-gradient(ellipse 40% 45% at 88% 35%, var(--slate), transparent 75%),
      radial-gradient(ellipse 30% 30% at 90% 10%, var(--taupe), transparent 75%),
      linear-gradient(180deg, var(--navy) 0%, var(--steel) 35%, var(--steel) 55%, var(--sky) 78%, var(--ice) 100%);
  }
  .art--disc {
    background:
      radial-gradient(ellipse 40% 40% at 80% 55%, var(--taupe), transparent 75%),
      radial-gradient(ellipse 40% 35% at 25% 20%, var(--ice), transparent 75%),
      linear-gradient(180deg, var(--sky) 0%, var(--steel) 50%, var(--navy) 80%, var(--slate) 100%);
  }
  .art--band {
    background:
      radial-gradient(ellipse 50% 25% at 50% 28%, var(--ice), transparent 75%),
      linear-gradient(180deg, #2f63a8 0%, var(--sky) 25%, var(--steel) 55%, var(--ink) 100%);
  }
  .art--inner {
    background:
      radial-gradient(ellipse 45% 35% at 30% 15%, var(--ice), transparent 75%),
      radial-gradient(ellipse 40% 40% at 80% 20%, var(--slate), transparent 75%),
      radial-gradient(ellipse 45% 40% at 65% 80%, #e9e3df, transparent 75%),
      linear-gradient(135deg, var(--sky) 0%, var(--steel) 40%, var(--taupe) 70%, var(--ice) 100%);
  }
  .band-name {
    position: absolute; font-family: "Oswald", sans-serif; font-weight: 300;
    color: var(--white); letter-spacing: 0.5px; white-space: nowrap;
  }
  .release-title {
    position: absolute; font-family: "Lexend Exa", sans-serif; font-weight: 600;
    color: var(--title-blue); letter-spacing: 1px; white-space: nowrap; text-transform: uppercase;
  }
  .front .band-name { left: 52px; top: 62px; font-size: 33px; }
  .front .release-title { left: 80px; top: 246px; font-size: 16px; }
  .tracklist {
    position: absolute; left: 41px; top: 38px; list-style: none;
    font-family: "Lexend Exa", sans-serif; font-weight: 600; font-size: 14.5px;
    line-height: 21px; color: var(--white); text-transform: uppercase; letter-spacing: 1px;
  }
  .credits {
    position: absolute; left: 0; right: 0; text-align: center;
    font-family: "Oswald", sans-serif; font-weight: 400; font-size: 6.2px;
    color: var(--ink); text-transform: uppercase;
  }
  .credits--a { top: 248px; }
  .credits--b { top: 263px; }
  .disc {
    position: absolute; width: 285px; height: 285px; border-radius: 50%; overflow: hidden;
    box-shadow: 0 2px 5px rgba(0,0,0,.25);
  }
  .disc__hole {
    position: absolute; left: 97px; top: 88px; width: 91px; height: 91px;
    border-radius: 50%; background: var(--page);
  }
  .disc .band-name { left: 38px; top: 176px; font-size: 29px; }
  .disc .release-title { left: 63px; top: 220px; font-size: 15px; }
</style>
</head>
<body>
<main class="sheet">
  <section class="panel front" style="left:29px; top:295px;" aria-label="Vorderseite">
    <div class="art art--front" role="img" aria-label="Low-Poly-Muster in Eisblau, Stahlblau und Taupe"></div>
    <h1 class="band-name">OKAPIMIND</h1>
    <h2 class="release-title">Open Gates</h2>
  </section>

  <section class="panel back" style="left:373px; top:295px;" aria-label="Rückseite">
    <div class="art art--back" role="img" aria-label="Low-Poly-Muster in Marineblau, Stahlblau und Eisweiß"></div>
    <ol class="tracklist">
      <li>1. Velvet Spoon</li>
      <li>2. Hold It Near</li>
      <li>3. Harbor Pike</li>
      <li>4. Can We Stay</li>
      <li>5. Brightest Edge</li>
    </ol>
    <p class="credits credits--a">Recording by Mustermann | Mix by Musterfrau &nbsp;|&nbsp; Mastering by Mustermännchen</p>
    <p class="credits credits--b">Recording by Mustermann | Mix by Musterfrau &nbsp;|&nbsp; Mastering by Mustermännchen</p>
  </section>

  <section class="disc" style="left:734px; top:295px;" aria-label="CD">
    <div class="art art--disc" role="img" aria-label="Low-Poly-Muster in Blau- und Taupetönen"></div>
    <div class="disc__hole"></div>
    <p class="band-name">OKAPIMIND</p>
    <p class="release-title">Open Gates</p>
  </section>

  <section class="panel inner-left" style="left:201px; top:620px;" aria-label="Innenseite links">
    <div class="art art--band" role="img" aria-label="Bandfoto: vier Musiker stehend vor blauem Low-Poly-Hintergrund"></div>
  </section>

  <section class="panel inner-right" style="left:545px; top:620px;" aria-label="Innenseite rechts">
    <div class="art art--inner" role="img" aria-label="Low-Poly-Muster in Grau, Blau und Taupe"></div>
  </section>
</main>
</body>
</html>
```